Dorian Vasko Consulting

I've the wording, and the rough layout. See attached MicroSoft Word File. I need a professional to make my postcard "look pretty".

Industry/Entity Type

Consulting

```html
<!DOCTYPE html>
<html lang="en">
<head>
<meta charset="utf-8">
<title>Dorian Vasko Consulting – Postcard</title>
<link rel="stylesheet" href="https://fonts.googleapis.com/css2?family=Arimo:wght@400;700&display=swap">
<style>
  :root {
    --card-red: #e8323a;
    --ink-white: #ffffff;
    --accent-yellow: #ffe500;
    --paper: #ffffff;
    --rule-grey: #7a7a7a;
    --edge-grey: #8c8c8c;
    --edge-blue: #4aa3df;
    --figure-shade: #d42a32;
    --ink-dark: #222222;
  }
  html, body {
    margin: 0;
    padding: 0;
    width: 866px;
    height: 1200px;
    overflow: hidden;
    background: var(--paper);
    font-family: "Arimo", Arial, sans-serif;
  }
  .sheet {
    position: relative;
    width: 800px;
    height: 1109px;
    transform: scale(1.0825);
    transform-origin: 0 0;
  }

  /* ---------- Front ---------- */
  .front {
    position: absolute;
    left: 0; top: 0;
    width: 800px; height: 533px;
    box-sizing: border-box;
    background: var(--card-red);
    border: 1px solid var(--edge-grey);
    color: var(--ink-white);
    overflow: hidden;
  }
  .brand-box {
    position: absolute;
    left: 27px; top: 28px;
    width: 148px; height: 54px;
    box-sizing: border-box;
    border: 1px solid var(--ink-white);
    display: flex; align-items: center; justify-content: center;
    text-align: center;
    font-size: 14px;
    line-height: 1.15;
    padding: 0 8px;
  }
  .headline {
    position: absolute;
    left: 343px; top: 18px;
    margin: 0;
    font-weight: 400;
    font-size: 41px;
    line-height: 50px;
    letter-spacing: -0.3px;
    white-space: nowrap;
  }
  .headline strong { font-weight: 700; font-size: 43px; }
  .headline .indent { display: block; padding-left: 129px; }
  .stair-chart {
    position: absolute;
    left: 0; top: 0;
  }
  .step-label {
    font-family: "Arimo", Arial, sans-serif;
    font-weight: 700;
    font-size: 11px;
    fill: var(--ink-white);
  }
  .step-num {
    font-family: "Arimo", Arial, sans-serif;
    font-weight: 700;
    font-size: 12px;
    fill: var(--ink-dark);
  }
  .copy-title {
    position: absolute;
    right: 20px; top: 243px;
    margin: 0;
    text-align: right;
    color: var(--accent-yellow);
    font-size: 14px;
    font-weight: 700;
    line-height: 20px;
  }
  .copy-body {
    position: absolute;
    left: 500px; top: 291px;
    width: 281px;
    font-size: 9.6px;
    line-height: 14.2px;
    letter-spacing: -0.15px;
    text-align: justify;
  }
  .copy-body p { margin: 0 0 14px; }

  /* ---------- Back ---------- */
  .back {
    position: absolute;
    left: 0; top: 576px;
    width: 800px; height: 533px;
  }
  .back-message {
    position: absolute;
    left: 0; top: 0;
    width: 430px; height: 533px;
    box-sizing: border-box;
    background: var(--card-red);
    border: 1px solid var(--edge-blue);
    color: var(--ink-white);
  }
  .photo-row { position: absolute; left: 0; top: 0; }
  .question-list {
    position: absolute;
    left: 27px; top: 214px;
    width: 380px;
    margin: 0; padding: 0;
    list-style: none;
    font-size: 10px;
    line-height: 15.2px;
    letter-spacing: -0.1px;
  }
  .pitch {
    position: absolute;
    left: 27px; top: 360px;
    width: 374px;
    margin: 0;
    font-size: 10px;
    line-height: 15.2px;
    letter-spacing: -0.15px;
    text-align: justify;
  }
  .web {
    position: absolute;
    left: 0; top: 467px;
    width: 430px;
    text-align: center;
    font-weight: 700;
    font-size: 14px;
  }
  .call {
    position: absolute;
    left: 0; top: 493px;
    width: 430px;
    text-align: center;
    font-weight: 700;
    font-size: 18.5px;
  }
  .address-side {
    position: absolute;
    left: 430px; top: 0;
    width: 370px; height: 533px;
    box-sizing: border-box;
    background: var(--paper);
    border: 1px solid var(--edge-grey);
    border-left: none;
  }
  .postage {
    position: absolute;
    left: 267px; top: 44px;
    margin: 0;
    font-weight: 700;
    font-size: 16.5px;
    line-height: 21px;
    color: var(--ink-dark);
  }
  .address-line {
    position: absolute;
    left: 57px;
    width: 263px;
    border-top: 1px solid var(--rule-grey);
  }
</style>
</head>
<body>
<div class="sheet">

  <section class="front">
    <div class="brand-box">Dorian Vasko Consulting</div>

    <h1 class="headline">Learn Small Business<br>Success Secrets<br>only <strong>“insiders”</strong><span class="indent">know about:</span></h1>

    <svg class="stair-chart" width="800" height="533" viewBox="0 0 800 533">
      <rect x="200" y="82" width="106" height="216" rx="10" fill="var(--figure-shade)"
            role="img" aria-label="Outline figure of a businessman with a briefcase climbing the steps"/>
      <polyline points="20,460 43,460 108,354 143,376 176,320 276,319 340,300 378,214 458,170"
                fill="none" stroke="#ffffff" stroke-width="3" stroke-linejoin="round"/>
      <polygon points="466,163 450,166 457,178" fill="#ffffff" stroke="#ffffff" stroke-width="2" stroke-linejoin="round"/>

      <g fill="#ffffff" stroke="#d42a32" stroke-width="1">
        <circle cx="43" cy="460" r="8"/>
        <circle cx="108" cy="354" r="8"/>
        <circle cx="143" cy="376" r="8"/>
        <circle cx="176" cy="320" r="8"/>
        <circle cx="276" cy="319" r="8"/>
        <circle cx="340" cy="300" r="8"/>
        <circle cx="378" cy="214" r="8"/>
      </g>
      <g class="step-num" text-anchor="middle">
        <text x="43" y="464">1</text>
        <text x="108" y="358">2</text>
        <text x="143" y="380">3</text>
        <text x="176" y="324">4</text>
        <text x="276" y="323">5</text>
        <text x="340" y="304">6</text>
        <text x="378" y="218">7</text>
      </g>
      <g class="step-label">
        <text x="56" y="468">Key of scccess behind insiders point</text>
        <text x="33" y="327">Key of scccess</text>
        <text x="33" y="342">behind insiders point</text>
        <text x="154" y="383">Key of scccess behind insiders point</text>
        <text x="179" y="342">Key of scccess</text>
        <text x="179" y="357">behind insiders point</text>
        <text x="289" y="328">Key of scccess behind insiders point</text>
        <text x="355" y="293">Key of scccess behind</text>
        <text x="355" y="308">insiders point</text>
        <text x="376" y="245">Key of scccess behind</text>
        <text x="376" y="260">insiders point</text>
      </g>
    </svg>

    <p class="copy-title">Here just 6-7 line copy<br>(Always&nbsp; communication simple )</p>

    <div class="copy-body">
      <p>“Insiders” who know the answers to these tricky business problems, get ahead in business and life. And the deeper their understanding to these tricky business problems, the more successful they become. They have very little stress from their businesses; they work very few hours by building their businesses into "auto pilot". They have more free time to enjoy life.</p>
      <p>If you don't know how to solve these tricky business problems, you will find yourself struggling with your businesses. You will find yourself working very long hours, and you have a lot of stress from running your business. If you are not even aware of the existence of this aspect of running a business, your business will not survive. You will become part of the statistic: 80% of businesses fail.</p>
    </div>
  </section>

  <section class="back">
    <div class="back-message">
      <svg class="photo-row" width="430" height="200" viewBox="0 0 430 200">
        <defs>
          <linearGradient id="photoTone" x1="0" y1="0" x2="0" y2="1">
            <stop offset="0" stop-color="#9a6a52"/>
            <stop offset="1" stop-color="#4e342c"/>
          </linearGradient>
        </defs>
        <polygon points="84,30 146,66 146,140 84,176 22,140 22,66"
                 fill="url(#photoTone)" stroke="#ffffff" stroke-width="2.5" stroke-dasharray="1.5 2.5"
                 role="img" aria-label="Photo of a smiling shop owner with a colleague in a cafe"/>
        <polygon points="211,48 273,84 273,156 211,192 149,156 149,84"
                 fill="url(#photoTone)" stroke="#ffffff" stroke-width="2.5" stroke-dasharray="1.5 2.5"
                 role="img" aria-label="Photo of two restaurant owners standing with arms crossed"/>
        <polygon points="344,30 406,66 406,140 344,176 282,140 282,66"
                 fill="url(#photoTone)" stroke="#ffffff" stroke-width="2.5" stroke-dasharray="1.5 2.5"
                 role="img" aria-label="Photo of a waitress holding a tray of oranges in a restaurant"/>
      </svg>

      <ol class="question-list">
        <li>1.How to make people want to have what you have for sale?</li>
        <li>2.How to turn new customers into repeat customers?</li>
        <li>3.How to make repeat customers comeback more often?</li>
        <li>4.How to spend less time with each customer, yet increase your profit on each business transaction?</li>
        <li>5.How to get more operating capital?</li>
        <li>6.How to buy low and sell high?</li>
        <li>7.How to manage employees and contractors?</li>
        <li>8.Which marketing methods are total waste of time and money?</li>
      </ol>

      <p class="pitch">Why do 80% of all businesses fail??? Because their owners didn't know what “business insiders” know. They worked very long hours, they had a lot of stresses and headaches, and in the end, due to their lack of business know-how, their businesses failed and they were left with a bunch of debt, a broken heart and sometimes a broken family too. Don't become one of them! Become a real “insider”, run a successful business without stress and enjoy life! To find out more:</p>

      <div class="web">www.VaskoInsiderSecrets.com</div>
      <div class="call">to Know Secreats call 555 014 2287</div>
    </div>

    <div class="address-side">
      <p class="postage">Postage<br>Paid</p>
      <div class="address-line" style="top:243px"></div>
      <div class="address-line" style="top:294px"></div>
      <div class="address-line" style="top:345px"></div>
      <div class="address-line" style="top:397px"></div>
    </div>
  </section>

</div>
</body>
</html>
```